Sophisticated, clean website reflecting my feminine, playful side to sell my abstract art,

I need a website no more than 3 pages to showcase my paintings, a little about me and some contact info. I do abstracts so looking for something a little edgy, yet feminine and current.
Updates

Hi there, These are some artists websites that I Iike: Marnelvoss.com (I like how airy it is) peterwallombry.com garethpolvens.com (I like how it scrolls) I'll need a place for a photo ( a headshot-i do not have it yet so I'll need to be able to upload that later) as well as an area for my bio. Also, it's important that I will be able to upload any new photos and descriptions easily so it should be user friendly. Lastly, I like in a sunny place so would like to have this seem upbeat and playful as that is how i like to paint. thanks-I'm trying to upload my photos now -

Target Market(s)

ppl ages 35-70 who want large scale art for their homes

Industry/Entity Type

art

Coding

Coded - Design and coding required

Number of Pages Required

3 page

Colors

Designer to choose colors to be used in the design.

Requirements
Must have
• photos of my art, a place for my bio, be easy to reach me. tasteful-nothing too "in your face" -my clients are pretty high end and organized. They like clean lines
Nice to have
• sophisticated background, muted tones in the back-similar clean font throughout-no cursive
Should not have
• too many dark areas. Too many blocks of color. Too serious.

```html
<!DOCTYPE html>
<html lang="en">
<head>
<meta charset="utf-8">
<title>Lorna Vessel Art – About Me</title>
<link rel="stylesheet" href="https://fonts.googleapis.com/css2?family=Playfair+Display:wght@600&family=Poppins:wght@300;400;500&family=Tinos&display=swap">
<style>
  :root {
    --ink: #111111;
    --body-text: #3a3a3a;
    --nav-muted: #5a5a5a;
    --rule: #cfcfcf;
    --footer-bg: #f8f8f8;
    --page-bg: #ffffff;
    --photo-top: #dfe6e7;
    --photo-mid: #8a6a58;
    --photo-low: #1c1a1a;
  }
  * { box-sizing: border-box; margin: 0; padding: 0; }
  html, body {
    width: 1200px; height: 1003px; overflow: hidden;
    background: var(--page-bg);
  }
  .page { position: relative; width: 1200px; height: 1003px; }

  .site-header {
    height: 66px;
    border-bottom: 1px solid var(--rule);
    display: flex; align-items: center; justify-content: center;
  }
  .site-title {
    font-family: "Playfair Display", serif;
    font-weight: 600;
    font-size: 35px;
    color: var(--ink);
    letter-spacing: -0.3px;
    padding-top: 4px;
  }

  .main-nav {
    position: absolute; top: 86px; left: 0; width: 1200px; height: 24px;
    font-family: "Poppins", sans-serif; font-size: 17px;
    text-transform: uppercase;
  }
  .main-nav a {
    position: absolute; transform: translateX(-50%);
    color: var(--nav-muted); text-decoration: none; white-space: nowrap;
  }
  .main-nav a.is-current { color: var(--ink); font-weight: 500; }

  .about-heading {
    position: absolute; left: 98px; top: 150px;
    font-family: "Poppins", sans-serif; font-weight: 400;
    font-size: 33px; color: var(--ink);
  }
  .about-bio {
    position: absolute; left: 102px; top: 210px; width: 492px;
    font-family: "Poppins", sans-serif; font-weight: 300;
    font-size: 17.2px; line-height: 35px; color: var(--body-text);
  }
  .about-bio p + p { margin-top: 16px; }

  .portrait {
    position: absolute; left: 618px; top: 168px; width: 481px; height: 586px;
    background: linear-gradient(180deg, var(--photo-top) 0%, #c9b3a3 35%, var(--photo-mid) 55%, var(--photo-low) 75%, #231f1f 100%);
  }

  .site-footer {
    position: absolute; left: 0; top: 849px; width: 1200px; height: 154px;
    background: var(--footer-bg);
  }
  .social-links {
    position: absolute; top: 40px; left: 0; width: 1200px;
    display: flex; justify-content: center; gap: 6px;
  }
  .social-links span {
    width: 38px; height: 38px; border: 1.5px solid #222; border-radius: 50%;
  }
  .copyright {
    position: absolute; top: 98px; left: 0; width: 1200px; text-align: center;
    font-family: "Tinos", serif; font-size: 16px; color: var(--ink);
  }
</style>
</head>
<body>
<div class="page">
  <header class="site-header">
    <h1 class="site-title">Lorna Vessel Art</h1>
  </header>

  <nav class="main-nav">
    <a class="is-current" href="#" style="left:312px">Home</a>
    <a href="#" style="left:476px">About Me</a>
    <a href="#" style="left:674px">My Paintings</a>
    <a href="#" style="left:870px">Contact</a>
  </nav>

  <h2 class="about-heading">About Me</h2>
  <div class="about-bio">
    <p>At vero eos et accusamus et iusto odio dignmos ducimus qui blanditiis praesentium voluptatum eniti atque corrupti quos dolores et quas molestturi sint occati cupiditate non provident, simue sunt in culpa qui officia deserunt mollitia animi, id est laborum et dolorum fuga. Et m quidem rerum facilis est et expedita distinctio. Nam libero tempore, cum soluta nobis est eligendi optio que nihil impedit quo minus id quod maxime placeat facere possimus, omnis voluptas assumenda est, omnis dolor repellendus.</p>
    <p>At vero eos et accusamus et iusto odio dignmos ducimus qui blanditiis praesentium voluptatum eniti atque corrupti quos dolores et quas molestturi sint occati cupiditate non provident, simue sunt in culpa qui officia deserunt mollitia animi, id est laborum et dolorum fuga. Et m quidem rerum facilis est et expedita distinctio.</p>
  </div>

  <div class="portrait" role="img" aria-label="Portrait photo of the artist outdoors by the water"></div>

  <footer class="site-footer">
    <div class="social-links">
      <span role="img" aria-label="Social profile link"></span>
      <span role="img" aria-label="Social profile link"></span>
      <span role="img" aria-label="Social profile link"></span>
    </div>
    <p class="copyright">©Copyright ©2022 Lorna Vessel Art. All Rights Reserved.</p>
  </footer>
</div>
</body>
</html>
```